Residential Remodeling Contractor needs updated business card

I need a new design for my business card.
Name of the company is Ridgefell Construction. I need a card that commands presence, strength, integrity. I have been in business for 28 years. I am a Residential Remodeling Contractor that covers all aspects of a residential remodel and build.

```html
<!DOCTYPE html>
<html lang="en">
<head>
<meta charset="utf-8">
<title>Ridgefell Construction – Business Card</title>
<link rel="stylesheet" href="https://fonts.googleapis.com/css2?family=Cinzel:wght@700&family=Arimo:wght@400&display=swap">
<style>
  :root {
    --stage: #1c1c1e;
    --card-blue: #1b3f86;
    --card-blue-light: #24509e;
    --card-blue-dark: #163572;
    --ink: #ffffff;
    --ink-soft: rgba(255,255,255,0.82);
  }
  * { box-sizing: border-box; margin: 0; padding: 0; }
  html, body {
    width: 1200px; height: 801px; overflow: hidden;
    background: var(--stage);
  }
  .stage {
    width: 1200px; height: 801px;
    display: flex; flex-direction: column; align-items: center; justify-content: center;
    gap: 36px;
  }
  .card {
    position: relative;
    width: 610px; height: 348px;
    border-radius: 24px;
    background: linear-gradient(135deg, var(--card-blue-light) 0%, var(--card-blue) 45%, var(--card-blue-dark) 100%);
    color: var(--ink);
    overflow: hidden;
  }

  /* Wordmark: plain name in the card's text font */
  .brand {
    display: flex; align-items: center;
    font-family: "Arimo", sans-serif; font-weight: 400;
    color: var(--ink);
    line-height: 1;
    white-space: nowrap;
  }
  .brand-square { background: var(--ink); flex: none; }

  .card--contact .brand { position: absolute; left: 40px; top: 62px; gap: 10px; font-size: 20px; }
  .card--contact .brand-square { width: 12px; height: 12px; }

  .card--brand { display: flex; align-items: center; justify-content: center; }
  .card--brand .brand { gap: 18px; font-size: 40px; }
  .card--brand .brand-square { width: 24px; height: 24px; }

  /* Contact side */
  .person {
    position: absolute; right: 60px; top: 54px; text-align: right;
  }
  .person-name {
    font-family: "Cinzel", serif; font-weight: 700; font-size: 21px; letter-spacing: 1px;
  }
  .person-title {
    font-family: "Arimo", sans-serif; font-size: 13px; color: var(--ink-soft); margin-top: 4px;
  }
  .edge-tab {
    position: absolute; right: 0; top: 38px;
    width: 40px; height: 30px; background: var(--ink);
    border-radius: 6px 0 0 6px;
  }

  .contact {
    position: absolute; left: 40px; bottom: 40px;
    font-family: "Arimo", sans-serif; font-size: 14px; color: var(--ink);
    list-style: none; line-height: 1.55;
  }
  .contact .address { margin-bottom: 10px; }
  .contact li { display: flex; align-items: center; gap: 9px; }
  .contact svg { width: 13px; height: 13px; flex: none; }
</style>
</head>
<body>
<main class="stage">

  <section class="card card--contact" aria-label="Business card, contact side">
    <div class="brand">
      <span class="brand-square"></span>
      <span class="brand-name">Ridgefell Construction</span>
    </div>

    <div class="edge-tab"></div>
    <div class="person">
      <p class="person-name">Daniel Hartwell</p>
      <p class="person-title">Owner &amp; Manager</p>
    </div>

    <ul class="contact">
      <li class="address">P.O. Box&nbsp; Street Name<br>Country Name AB, A5B 521</li>
      <li>
        <svg viewBox="0 0 16 16" aria-hidden="true"><path fill="#fff" d="M3.6 1.2l2.3 2.6-1.4 1.9c.9 2 2.4 3.5 4.3 4.4l1.9-1.4 2.6 2.3-1.3 2.5C6.9 13.2 2.7 9 1.1 3.9z"/></svg>
        555 014 2290
      </li>
      <li>
        <svg viewBox="0 0 16 16" aria-hidden="true"><rect x="1" y="3" width="14" height="10" rx="1.5" fill="#fff"/><path d="M1.5 4l6.5 5 6.5-5" stroke="#1b3f86" stroke-width="1.4" fill="none"/></svg>
        info@ridgefellconstruction.com
      </li>
      <li>
        <svg viewBox="0 0 16 16" aria-hidden="true"><circle cx="8" cy="8" r="6.5" fill="none" stroke="#fff" stroke-width="1.4"/><ellipse cx="8" cy="8" rx="2.8" ry="6.5" fill="none" stroke="#fff" stroke-width="1.2"/><path d="M1.5 8h13" stroke="#fff" stroke-width="1.2"/></svg>
        www.ridgefellconstruction.com
      </li>
    </ul>
  </section>

  <section class="card card--brand" aria-label="Business card, brand side">
    <div class="brand">
      <span class="brand-square"></span>
      <span class="brand-name">Ridgefell Construction</span>
    </div>
  </section>

</main>
</body>
</html>
```